Redo our website for our Robotics company

We sell robotic equipment to the restaurant industry. Our current robot, is a cooking robot that cooks up to 15 lbs of food. We will provide a prior website as well as brand guidelines. We plan on using wordpress and take advantage of wordpress's visual (no code) editor.

Current website - https://kelvatrix88.com/ (please note we are only selling Tammo now and no longer selling Plavo+

We want someone to take our existing content and design the website as well as layout our content we provide. Here's a suggested site layout:

✅ KelvaTrix88 Website Wireframe / Site Map
1. Home

Purpose: Introduce Tammo, establish credibility, drive demo requests.

Sections:

Hero Section

Headline: “Meet Tammo — Your New Robotic Chef for High-Volume, Consistent Cooking.”

Sub-headline: Increase throughput. Reduce labor. Deliver perfect food every time.

CTA: Request a Demo + Watch Tammo Cook

Visual: Video loop or hero animation of Tammo in action.

How Tammo Works (3-4 steps)

Step cards: Load Ingredients → Select Recipe → Tammo Cooks → Serve

Icons and short explanations.

Key Benefits

Labor savings

Zero inconsistency

24/7 uptime

Throughput increases (30–50% faster)

Health & safety compliance

Who It’s For

QSR restaurants

Fast casual

Catering/commissaries

Ghost kitchens

Case Studies / Testimonials

Logo bar + quotes

“Tammo helped us reduce cooking times by 40%.”

Video Section

“Watch Tammo cook a full batch from start to finish.”

CTA Section

Big banner: Book a Demo

2. Product: “Meet Tammo”

Purpose: Deep dive into hardware, software, safety, reliability.

Sections:

Overview

What Tammo is

What tasks it automates

Where it fits in a kitchen

Hardware Features

High-temperature cooking chamber

Precision sensors

Automated stirring

Automated dispensing

Safety mechanisms (locking lids, auto-shutoff)

Software & AI

Recipe automation

IoT dashboard

Remote monitoring

Predictive maintenance

Specs Table

Dimensions

Power requirements

Capacity (lbs per batch)

Safety certifications

Gallery

Close-ups, installation photos, process shots

CTA: Request a Demo

3. Solutions

Purpose: Show that Tammo solves real operational problems.

Sub-pages or sections:

For Quick-Service Restaurants

Reduce labor cost

Speed up peak-hour demand

For Catering & Commissaries

Large-batch consistency

Automate repetitive cooking tasks

For High-Growth Chains

Replicable quality across multiple locations

Centralized recipe control

Each solution page includes:

A problem statement

How Tammo solves it

Metrics / KPIs

Relevant testimonial

CTA

4. ROI / Economics

Purpose: Sell the financial story clearly.

Sections:

Savings Calculator

Labor hours saved

Cost savings

Throughput increases

Food waste reduction

Before & After Comparison

Traditional kitchen vs. robotic kitchen

Sample ROI

“Payback in as little as 3–6 months.”

Download Full ROI Report (PDF)

5. Case Studies

Purpose: Social proof + real results.

Structure for each case study:

Customer background

Problem

Implementation

KPIs achieved

Labor savings

Consistency improvements

Cooking speed

Quote + photos/video

6. Pricing

Purpose: Start a commercial conversation.

Include:

Subscription model (monthly / annual)

Hardware leasing or purchase options

Installation + training

Support level

CTA to book a sales call

7. About

Purpose: Build trust.

Sections:

Mission statement

Founding team

Advisors/partners

“Why we built Tammo”

8. Resources

Purpose: SEO + education.

Subpages:

Blog (e.g., “The Future of Automated Kitchens”)

Whitepapers

Technical documentation

Product videos

9. Contact

General inquiry form

Sales contact

Support portal

Careers

```html
<!DOCTYPE html>
<html lang="en">
<head>
<meta charset="utf-8">
<title>KelvaTrix88 — Meet Tammo</title>
<link href="https://fonts.googleapis.com/css2?family=Oswald:wght@500;600;700&family=Montserrat:wght@400;500;600;700&display=swap" rel="stylesheet">
<style>
:root{
  --red:#ee2f24;
  --orange:#f5632a;
  --navy:#0c2452;
  --dark:#1b1b1d;
  --ink:#222;
  --muted:#555;
  --card-border:#e3e6ee;
  --white:#fff;
}
*{box-sizing:border-box;margin:0;padding:0}
html,body{width:1200px;height:5124px;overflow:hidden}
body{position:relative;background:var(--white);font-family:'Montserrat',sans-serif;color:var(--ink)}
a{text-decoration:none}
.abs{position:absolute}
h1,h2,h3,h4{font-family:'Oswald',sans-serif;text-transform:uppercase;font-weight:600}
.btn{position:absolute;display:flex;align-items:center;justify-content:center;font-size:14px;font-weight:500;color:#fff;text-decoration:none;
  background:linear-gradient(90deg,var(--red),var(--orange));clip-path:polygon(0 0,100% 0,96% 100%,0 100%);border-radius:6px 0 0 6px}
.btn.ghost{background:#fff;color:var(--orange)}
.logo{font-family:'Montserrat',sans-serif;font-weight:700;font-size:34px;color:var(--red);letter-spacing:-.5px}
.logo.light{color:#fff}
/* header */
.site-header{position:absolute;top:0;left:0;width:1200px;height:100px;background:#fff}
.nav{position:absolute;top:64px;left:462px;display:flex;font-size:15px}
.nav a{color:#222;margin-right:44px}
.nav a.active{color:var(--red);border-bottom:2px solid var(--red);padding-bottom:3px}
/* hero */
.hero-bg{position:absolute;top:100px;left:0}
.hero-eyebrow{color:var(--red);font-size:54px;line-height:60px}
.hero-title{color:#fff;font-size:43px;line-height:54px;font-weight:600}
.hero-sub{color:#fff;font-size:16px;line-height:28px}
/* headings */
.sec-title{color:var(--navy);font-size:46px;text-align:center;width:1200px;left:0}
.sec-lead{font-size:15px;line-height:27px;color:var(--muted);text-align:center;width:680px;left:260px}
/* steps */
.step{position:absolute;top:952px;width:236px;height:324px;border:1px solid var(--card-border);border-radius:14px;box-shadow:0 6px 18px rgba(12,36,82,.08);text-align:center;overflow:hidden;background:#fff}
.icon-box{width:80px;height:80px;margin:44px auto 0;border-radius:10px;background:linear-gradient(135deg,var(--orange),var(--red));display:flex;align-items:center;justify-content:center}
.step h3{font-size:18px;color:var(--navy);margin-top:18px;font-weight:600}
.step p{font-size:13px;line-height:24px;color:var(--muted);margin:10px 18px 0}
.step .num{font-family:'Oswald',sans-serif;font-size:56px;font-weight:700;color:rgba(238,47,36,.13);margin-top:-2px}
/* about */
.about-title{color:var(--navy);font-size:46px}
.about-text{font-size:15px;line-height:31px;color:var(--muted);text-align:justify;width:440px}
/* benefits */
.benefit{position:absolute;top:2160px;width:250px;text-align:center;color:#fff}
.benefit .ic{width:92px;height:82px;margin:0 auto;background:#fff;border-radius:12px;clip-path:polygon(10% 0,100% 0,90% 100%,0 100%);display:flex;align-items:center;justify-content:center}
.benefit h3{font-size:21px;margin-top:26px;font-weight:600}
.benefit p{font-size:14px;line-height:25px;margin:8px 14px 0}
/* audience */
.aud{position:absolute;top:2752px;width:238px;height:348px;border-radius:14px;overflow:hidden;background:var(--navy)}
.aud .ph{height:292px}
.aud h3{color:#fff;font-size:17px;text-align:center;line-height:56px;font-weight:600}
/* testimonial */
.quote-h{color:var(--navy);font-size:48px;line-height:56px;text-align:center;width:1200px;left:0}
/* footer */
.foot-h{color:#fff;font-size:23px;font-weight:600}
.foot-list{list-style:none;color:#fff;font-size:13px}
.foot-list li{display:flex;align-items:flex-start;gap:14px;line-height:18px;margin-bottom:18px}
.foot-list svg{flex:none;margin-top:1px}
</style>
</head>
<body>

<header class="site-header">
  <div class="abs logo" style="left:110px;top:26px">KelvaTrix88</div>
  <nav class="nav">
    <a class="active" href="#">Home</a><a href="#">Solutions</a><a href="#">Economics</a><a href="#">Pricing</a><a href="#">About Us</a><a href="#" style="margin-right:0">Resources</a>
  </nav>
  <a class="btn" href="#" style="left:960px;top:12px;width:130px;height:40px;font-size:13px">Contact Us</a>
</header>

<section class="hero">
  <svg class="hero-bg" width="1200" height="630" viewBox="0 0 1200 630">
    <defs>
      <linearGradient id="heroPhoto" x1="0" x2="1" y1="0" y2="1">
        <stop offset="0" stop-color="#2a2a2c"/><stop offset="1" stop-color="#55585c"/>
      </linearGradient>
      <linearGradient id="stripe" x1="0" x2="1"><stop offset="0" stop-color="#ee2f24"/><stop offset="1" stop-color="#f5632a"/></linearGradient>
    </defs>
    <polygon points="0,0 1200,0 1200,440 340,620 0,490" fill="#1e1e20"/>
    <polygon role="img" aria-label="Row of Tammo cooking robots with touch screens in a commercial kitchen" points="560,0 1200,0 1200,440 560,575" fill="url(#heroPhoto)"/>
    <polygon points="340,620 1200,440 1200,470 340,630" fill="url(#stripe)"/>
    <polygon points="300,612 340,620 340,630" fill="url(#stripe)"/>
  </svg>
  <h1 class="abs hero-eyebrow" style="left:110px;top:178px">Meet Tammo</h1>
  <h2 class="abs hero-title" style="left:110px;top:240px;width:430px">Your new robotic chef for high-volume, consistent cooking.</h2>
  <p class="abs hero-sub" style="left:110px;top:414px;width:380px">Increase throughput. Reduce labor. Deliver perfect food every time.</p>
  <a class="btn" href="#" style="left:110px;top:487px;width:186px;height:44px">Request a Demo</a>
  <a class="btn ghost" href="#" style="left:310px;top:487px;width:212px;height:44px">Watch Tammo Cook</a>
</section>

<section class="how">
  <h2 class="abs sec-title" style="top:806px">How Tammo Works</h2>
  <p class="abs sec-lead" style="top:864px">Service robots, such as our cutting-edge culinary assistants, are not just a nod to the future- they are a robust solution to today's burgeoning challenges.</p>

  <div class="step" style="left:110px">
    <div class="icon-box"><svg width="42" height="42" viewBox="0 0 24 24" fill="none" stroke="#fff" stroke-width="1.8"><path d="M5 9h14l-1.5 11h-11z"/><path d="M9 9V6a3 3 0 0 1 6 0v3"/></svg></div>
    <h3>Load Ingredients</h3>
    <p>At vero eos et accusamus et iusto odio dignissimos duci mus qui blanditiis praes entium volupta</p>
    <div class="num">01</div>
  </div>
  <div class="step" style="left:358px">
    <div class="icon-box"><svg width="42" height="42" viewBox="0 0 24 24" fill="none" stroke="#fff" stroke-width="1.8"><rect x="5" y="4" width="12" height="16" rx="1"/><path d="M8 8h6M8 12h6M8 16h3"/></svg></div>
    <h3>Select Recipe</h3>
    <p>At vero eos et accusamus et iusto odio dignissimos duci mus qui blanditiis praes entium volupta</p>
    <div class="num">02</div>
  </div>
  <div class="step" style="left:606px">
    <div class="icon-box"><svg width="42" height="42" viewBox="0 0 24 24" fill="none" stroke="#fff" stroke-width="1.8"><path d="M3 12h18a9 7 0 0 1-18 0z"/><path d="M14 10l6-6"/></svg></div>
    <h3>Tammo Cooks</h3>
    <p>At vero eos et accusamus et iusto odio dignissimos duci mus qui blanditiis praes entium volupta</p>
    <div class="num">03</div>
  </div>
  <div class="step" style="left:854px">
    <div class="icon-box"><svg width="42" height="42" viewBox="0 0 24 24" fill="none" stroke="#fff" stroke-width="1.8"><path d="M4 16a8 8 0 0 1 16 0z"/><path d="M2 19h20M12 6v2"/></svg></div>
    <h3>Serve</h3>
    <p>At vero eos et accusamus et iusto odio dignissimos duci mus qui blanditiis praes entium volupta</p>
    <div class="num">04</div>
  </div>
</section>

<section class="benefits-band">
  <svg class="abs" style="left:0;top:1870px" width="1200" height="670" viewBox="0 0 1200 670">
    <defs>
      <linearGradient id="band" x1="0" x2="1" y1="0" y2="0"><stop offset="0" stop-color="#f0702f"/><stop offset=".5" stop-color="#ef3f2a"/><stop offset="1" stop-color="#dc1c24"/></linearGradient>
    </defs>
    <polygon points="588,2 1200,140 1200,670 0,670 0,90 110,60 588,60" fill="url(#band)"/>
    <polygon points="588,0 1200,128 1200,160 588,40" fill="#0c2452"/>
  </svg>
  <h2 class="abs" style="left:0;top:2058px;width:1200px;text-align:center;color:#fff;font-size:44px">KelvaTrix88's Key Benefits</h2>
  <div class="benefit" style="left:100px"><div class="ic"><svg width="40" height="40" viewBox="0 0 24 24" fill="none" stroke="#ee2f24" stroke-width="2"><path d="M4 14a8 8 0 0 1 16 0z"/><path d="M3 17h18"/></svg></div><h3>Labor Savings</h3><p>Nam libero tempore, cum soluta nobis est eligendi optio cumque nihil impedit</p></div>
  <div class="benefit" style="left:350px"><div class="ic"><svg width="40" height="40" viewBox="0 0 24 24" fill="none" stroke="#ee2f24" stroke-width="2"><circle cx="12" cy="12" r="7"/><circle cx="12" cy="12" r="3"/><path d="M12 2v4M12 18v4M2 12h4M18 12h4"/></svg></div><h3>Zero Inconsistency</h3><p>Nam libero tempore, cum soluta nobis est eligendi optio cumque nihil impedit</p></div>
  <div class="benefit" style="left:600px"><div class="ic"><svg width="40" height="40" viewBox="0 0 24 24" fill="none" stroke="#ee2f24" stroke-width="2"><circle cx="12" cy="12" r="9"/><path d="M12 7v5l3 2"/></svg></div><h3>24/7 Uptime</h3><p>Nam libero tempore, cum soluta nobis est eligendi optio cumque nihil impedit</p></div>
  <div class="benefit" style="left:850px"><div class="ic"><svg width="40" height="40" viewBox="0 0 24 24" fill="none" stroke="#ee2f24" stroke-width="2"><path d="M12 20s-8-5-8-11a4 4 0 0 1 8-1 4 4 0 0 1 8 1c0 6-8 11-8 11z"/><path d="M9 11l2 2 4-4"/></svg></div><h3>Health &amp; Safety</h3><p>Nam libero tempore, cum soluta nobis est eligendi optio cumque nihil impedit</p></div>
  <a class="btn ghost" href="#" style="left:494px;top:2410px;width:212px;height:42px">View More Benefits</a>
</section>

<section class="about">
  <div class="abs" role="img" aria-label="Stainless steel commercial kitchen with extraction hoods" style="left:110px;top:1402px;width:478px;height:570px;border-radius:22px;background:linear-gradient(160deg,#3a3d42,#14161a 70%);box-shadow:0 10px 30px rgba(0,0,0,.2)"></div>
  <h2 class="abs about-title" style="left:652px;top:1446px">Who We Are</h2>
  <p class="abs about-text" style="left:652px;top:1514px">In an era where the gig economy reshapes labor dynamics, minimum wages rise, and labor disputes intensify, the food service industry stands at a crucial crossroads.</p>
  <p class="abs about-text" style="left:652px;top:1668px">Service robots, such as our cutting-edge culinary assistants, are not just a nod to the future—they are a robust solution to today's burgeoning challenges.</p>
  <a class="btn" href="#" style="left:652px;top:1790px;width:136px;height:42px">Read More</a>
</section>

<section class="audience">
  <h2 class="abs sec-title" style="top:2612px">Who It's For</h2>
  <p class="abs sec-lead" style="top:2672px">Service robots, such as our cutting-edge culinary assistants, are not just a nod to the future- they are a robust solution to today's burgeoning challenges.</p>
  <div class="aud" style="left:110px"><div class="ph" role="img" aria-label="Quick service restaurant counter with prepared food" style="background:linear-gradient(180deg,#3b2a1c,#a4672a)"></div><h3>QSR Restaurants</h3></div>
  <div class="aud" style="left:358px"><div class="ph" role="img" aria-label="Fast casual restaurant interior with wooden counter" style="background:linear-gradient(180deg,#2b1f18,#8a5a34)"></div><h3>Fast Casual</h3></div>
  <div class="aud" style="left:606px"><div class="ph" role="img" aria-label="Catering buffet with plated appetizers" style="background:linear-gradient(180deg,#b8c3cc,#d9d3c8)"></div><h3>Catering/Commissaries</h3></div>
  <div class="aud" style="left:854px"><div class="ph" role="img" aria-label="Ghost kitchen counter with chef hat and utensils" style="background:linear-gradient(180deg,#5a4634,#c9b79f)"></div><h3>Ghost Kitchens</h3></div>
</section>

<section class="testimonial">
  <svg class="abs" style="left:566px;top:3208px" width="68" height="60" viewBox="0 0 68 60"><path d="M28 0C12 6 0 18 0 36a14 14 0 1 0 14-14c0-8 6-15 16-20z M66 0C50 6 38 18 38 36a14 14 0 1 0 14-14c0-8 6-15 16-20z" fill="#ee2f24"/></svg>
  <h2 class="abs quote-h" style="top:3300px">Tammo helped us<br>reduce cooking times by 40%.</h2>
  <p class="abs sec-lead" style="top:3428px">At vero eos et accusamus et iusto odio dignissimos ducimus qui blanditiis praesentium voluptatum deleniti atque corrupti quos dolores et quas molestias excepturi sint occaecati cupiditate non provident, similique sunt in culpa</p>
  <div class="abs" style="left:0;width:1200px;top:3528px;text-align:center;color:#f5632a;font-size:15px;letter-spacing:2px">★★★★★</div>
  <div class="abs" style="left:0;width:1200px;top:3556px;text-align:center;color:#f5632a;font-size:14px;font-weight:700;letter-spacing:1px">DANA KESSLER</div>
  <div class="abs" style="left:534px;top:3592px;width:132px;height:58px;border-radius:10px;background:#fff;box-shadow:0 4px 14px rgba(0,0,0,.12);display:flex;align-items:center;justify-content:center;gap:8px">
    <span style="width:14px;height:14px;border-radius:50%;background:var(--navy)"></span><span style="font-weight:600;font-size:18px;color:var(--navy)">Corvale</span>
  </div>
  <div class="abs" style="left:576px;top:3672px;display:flex;gap:6px"><i style="width:8px;height:8px;border-radius:50%;background:#444"></i><i style="width:8px;height:8px;border-radius:50%;background:#ccc"></i><i style="width:8px;height:8px;border-radius:50%;background:#ccc"></i><i style="width:8px;height:8px;border-radius:50%;background:#ccc"></i></div>
</section>

<section class="video">
  <div class="abs" style="left:165px;top:3775px;width:870px;height:570px;border-radius:28px;overflow:hidden;border:2px solid var(--red);box-shadow:0 12px 30px rgba(0,0,0,.18)">
    <div class="abs" style="left:0;top:0;width:125px;height:570px;background:var(--red)">
      <div class="abs" style="left:62px;top:285px;transform:translate(-50%,-50%) rotate(-90deg);white-space:nowrap;color:#fff;font-family:'Oswald',sans-serif;text-transform:uppercase;text-align:center">
        <div style="font-size:40px;font-weight:600;line-height:44px">Watch Tammo Cook</div>
        <div style="font-size:27px;font-weight:500;line-height:32px">A full batch from start to finish</div>
      </div>
    </div>
    <div class="abs" role="img" aria-label="Trade show booth with Tammo demonstration and visitors" style="left:125px;top:0;width:745px;height:570px;background:linear-gradient(135deg,#3a4354,#1a1d24 60%,#2a2f3a)"></div>
    <div class="abs" style="left:796px;top:498px;width:56px;height:56px;border-radius:50%;background:var(--red);display:flex;align-items:center;justify-content:center;border:4px solid #fff"><svg width="18" height="18" viewBox="0 0 18 18"><path d="M5 3l10 6-10 6z" fill="#fff"/></svg></div>
  </div>
  <p class="abs sec-lead" style="top:4400px">At vero eos et accusamus et iusto odio dignissimos ducimus qui blanditiis praesentium voluptatum deleniti atque corrupti quos dolores et quas molestias excepturi sint occaecati cupiditate non provident, similique sunt in culpa</p>
  <a class="btn" href="#" style="left:522px;top:4498px;width:156px;height:44px">Book a Demo</a>
</section>

<footer class="site-footer">
  <svg class="abs" style="left:0;top:4650px" width="1200" height="474" viewBox="0 0 1200 474">
    <defs><linearGradient id="fstripe" x1="0" x2="1"><stop offset="0" stop-color="#f0702f"/><stop offset="1" stop-color="#e42a22"/></linearGradient></defs>
    <polygon points="360,14 1200,70 1200,90 0,160 0,130" fill="url(#fstripe)"/>
    <polygon points="0,140 1200,76 1200,474 0,474" fill="#0c2452"/>
  </svg>
  <div class="abs logo light" style="left:110px;top:4816px;font-size:30px">KelvaTrix88</div>
  <h4 class="abs foot-h" style="left:392px;top:4808px">Quick Links</h4>
  <ul class="abs foot-list" style="left:392px;top:4858px">
    <li><svg width="14" height="14" viewBox="0 0 14 14"><circle cx="7" cy="7" r="6" fill="#fff"/><path d="M5 4l4 3-4 3" stroke="#0c2452" stroke-width="1.6" fill="none"/></svg>Why Service Robots?</li>
    <li><svg width="14" height="14" viewBox="0 0 14 14"><circle cx="7" cy="7" r="6" fill="#fff"/><path d="M5 4l4 3-4 3" stroke="#0c2452" stroke-width="1.6" fill="none"/></svg>Service Robots</li>
    <li><svg width="14" height="14" viewBox="0 0 14 14"><circle cx="7" cy="7" r="6" fill="#fff"/><path d="M5 4l4 3-4 3" stroke="#0c2452" stroke-width="1.6" fill="none"/></svg>Cooking Robots</li>
    <li><svg width="14" height="14" viewBox="0 0 14 14"><circle cx="7" cy="7" r="6" fill="#fff"/><path d="M5 4l4 3-4 3" stroke="#0c2452" stroke-width="1.6" fill="none"/></svg>Contact Us</li>
    <li><svg width="14" height="14" viewBox="0 0 14 14"><circle cx="7" cy="7" r="6" fill="#fff"/><path d="M5 4l4 3-4 3" stroke="#0c2452" stroke-width="1.6" fill="none"/></svg>Request a Demo</li>
  </ul>
  <h4 class="abs foot-h" style="left:652px;top:4808px">Contact Info</h4>
  <ul class="abs foot-list" style="left:652px;top:4856px;width:250px">
    <li style="line-height:36px;margin-bottom:0"><svg width="14" height="16" viewBox="0 0 14 16" style="margin-top:10px"><path d="M7 1a5 5 0 0 1 5 5c0 4-5 9-5 9S2 10 2 6a5 5 0 0 1 5-5z" fill="#fff"/><circle cx="7" cy="6" r="2" fill="#0c2452"/></svg><span>482 W Harlow Ave Ste 310, Larkspur, CA, United States, 94939</span></li>
    <li style="margin-top:8px"><svg width="14" height="14" viewBox="0 0 24 24"><path d="M5 3h4l2 5-3 2a12 12 0 0 0 6 6l2-3 5 2v4a2 2 0 0 1-2 2A18 18 0 0 1 3 5a2 2 0 0 1 2-2z" fill="#fff"/></svg>+1 (555) 014 2276</li>
    <li><svg width="14" height="14" viewBox="0 0 24 24"><rect x="2" y="5" width="20" height="14" rx="2" fill="#fff"/><path d="M3 6l9 7 9-7" stroke="#0c2452" stroke-width="2" fill="none"/></svg>info@kelvatrix88.com</li>
  </ul>
  <h4 class="abs foot-h" style="left:965px;top:4808px">Follow Us</h4>
  <ul class="abs foot-list" style="left:965px;top:4858px">
    <li><svg width="12" height="12"><rect width="12" height="12" rx="2" fill="#fff"/></svg>Linkwave</li>
    <li><svg width="12" height="12"><rect width="12" height="12" rx="2" fill="#fff"/></svg>Photoloop</li>
    <li><svg width="12" height="12"><circle cx="6" cy="6" r="6" fill="#fff"/></svg>Chirpline</li>
  </ul>
  <div class="abs" style="left:110px;top:5066px;width:980px;height:1px;background:rgba(255,255,255,.35)"></div>
  <a class="abs" href="#" style="left:948px;top:5046px;width:142px;height:42px;border-radius:21px 0 0 21px;background:#fff;color:var(--red);font-size:14px;font-weight:500;display:flex;align-items:center;justify-content:center;gap:8px">
    <svg width="14" height="14" viewBox="0 0 24 24"><path d="M3 5h18v11H8l-5 4z" fill="none" stroke="#ee2f24" stroke-width="2"/></svg>Let's Talk</a>
  <p class="abs" style="left:0;top:5094px;width:1200px;text-align:center;color:#fff;font-size:13px">(C) Copyright 2025 | All Rights Reserved</p>
</footer>

</body>
</html>
```